Business card design

We need a business card designed completed for a new company. We are a company that works with associations, schools to convert their older text/DVDs into dynamic online and mobile programs. Our initial platform is designed for the legal associations and will enable their lawyers to access their content such as forms, videos, case law and support materials anywhere, anytime. We are also focused on Project Management Associations, Financial Management Associations and IT Associations.

I would like for the business card to have the following information:

Logo

Kent marrowby

President and CEO

kmarrowby@trevantiq.example

Mobile: 555-374-9160

www.trevantiq.example

Tag line: Transforming content into a mobile platform    

I would like it to be double sided, use the colours of the logo, tie into the mobile world

 

Industry/Entity Type

Legal

Logo Text

Trevantiq

```html
<!DOCTYPE html>
<html lang="en">
<head>
<meta charset="utf-8">
<title>Trevantiq business card</title>
<link rel="stylesheet" href="https://fonts.googleapis.com/css2?family=Open+Sans:wght@400;600;700&display=swap">
<style>
  :root {
    --stage: #ebe8e4;
    --card-grey: #939393;
    --card-white: #ffffff;
    --band-grey: #9a9a9a;
    --accent-dark: #666666;
    --ink: #222222;
    --ink-soft: #555555;
    --paper: #ffffff;
  }
  * { box-sizing: border-box; margin: 0; padding: 0; }
  html, body { width: 1200px; height: 800px; overflow: hidden; }
  body {
    position: relative;
    background: var(--stage);
    font-family: "Open Sans", Arial, sans-serif;
    color: var(--ink);
  }
  .side-label {
    position: absolute;
    width: 508px;
    text-align: center;
    font-size: 20px;
    color: var(--ink);
  }
  .card {
    position: absolute;
    width: 508px;
    height: 290px;
    border-radius: 22px;
    overflow: hidden;
    box-shadow: 0 4px 12px rgba(0,0,0,.25);
  }
  .card--grey { background: var(--card-grey); }
  .card--white { background: var(--card-white); }

  .wordmark {
    position: absolute;
    font-weight: 700;
    line-height: 1;
    letter-spacing: -0.5px;
  }
  .card--grey .wordmark { color: var(--paper); }
  .card--white .wordmark { color: var(--accent-dark); }
  .wordmark--small { left: 82px; top: 52px; font-size: 54px; }
  .wordmark--large { left: 0; width: 100%; text-align: center; top: 92px; font-size: 80px; }

  .name-band {
    position: absolute;
    left: 0; top: 136px;
    width: 436px; height: 32px;
    display: flex; align-items: center; justify-content: center;
    gap: 5px;
  }
  .card--grey .name-band { background: var(--paper); color: var(--accent-dark); }
  .card--white .name-band { background: var(--band-grey); color: var(--paper); }
  .name-band .person { font-weight: 700; font-size: 15px; }
  .name-band .role { font-size: 12px; padding-top: 2px; }
  .band-block {
    position: absolute;
    left: 443px; top: 136px;
    width: 65px; height: 32px;
    background: var(--accent-dark);
  }

  .contact-list {
    position: absolute;
    left: 33px; top: 210px;
    list-style: none;
    font-size: 13px;
    line-height: 21px;
    color: var(--ink);
  }
  .contact-list li { display: flex; align-items: center; gap: 6px; }
  .contact-list svg { width: 10px; height: 10px; fill: none; stroke: var(--ink-soft); stroke-width: 1.4; }

  .tagline {
    position: absolute;
    left: 282px; top: 230px;
    font-size: 15px;
    line-height: 20px;
    color: var(--ink);
  }
  .web-address {
    position: absolute;
    left: 0; width: 100%;
    bottom: 18px;
    text-align: center;
    font-size: 15px;
    letter-spacing: 3px;
    color: var(--ink);
  }
</style>
</head>
<body>

<div class="side-label" style="left:72px; top:50px;">Front</div>
<section class="card card--grey" style="left:72px; top:90px;">
  <div class="wordmark wordmark--small">Trevantiq</div>
  <div class="name-band"><span class="person">Kent marrowby,</span><span class="role">President and CEO</span></div>
  <div class="band-block"></div>
  <ul class="contact-list">
    <li><svg viewBox="0 0 10 10"><rect x="2.5" y="0.8" width="5" height="8.4" rx="1"/></svg>555-374-9160</li>
    <li><svg viewBox="0 0 10 10"><rect x="0.8" y="2" width="8.4" height="6"/><path d="M0.8 2 L5 5.5 L9.2 2"/></svg>kmarrowby@trevantiq.example</li>
    <li><svg viewBox="0 0 10 10"><circle cx="5" cy="5" r="4.2"/><path d="M0.8 5 H9.2 M5 0.8 C2.5 3 2.5 7 5 9.2 M5 0.8 C7.5 3 7.5 7 5 9.2"/></svg>www.trevantiq.example</li>
  </ul>
  <p class="tagline">Transforming content<br>into a mobile platform</p>
</section>

<div class="side-label" style="left:628px; top:50px;">Back - 1</div>
<section class="card card--white" style="left:628px; top:90px;">
  <div class="wordmark wordmark--small">Trevantiq</div>
  <div class="name-band"><span class="person">Kent marrowby,</span><span class="role">President and CEO</span></div>
  <div class="band-block"></div>
  <ul class="contact-list">
    <li><svg viewBox="0 0 10 10"><rect x="2.5" y="0.8" width="5" height="8.4" rx="1"/></svg>555-374-9160</li>
    <li><svg viewBox="0 0 10 10"><rect x="0.8" y="2" width="8.4" height="6"/><path d="M0.8 2 L5 5.5 L9.2 2"/></svg>kmarrowby@trevantiq.example</li>
    <li><svg viewBox="0 0 10 10"><circle cx="5" cy="5" r="4.2"/><path d="M0.8 5 H9.2 M5 0.8 C2.5 3 2.5 7 5 9.2 M5 0.8 C7.5 3 7.5 7 5 9.2"/></svg>www.trevantiq.example</li>
  </ul>
  <p class="tagline">Transforming content<br>into a mobile platform</p>
</section>

<div class="side-label" style="left:64px; top:410px;">Back - 2</div>
<section class="card card--grey" style="left:64px; top:450px;">
  <div class="wordmark wordmark--large">Trevantiq</div>
  <div class="web-address">www.trevantiq.example</div>
</section>

<div class="side-label" style="left:628px; top:410px;">Back - 3</div>
<section class="card card--white" style="left:628px; top:450px;">
  <div class="wordmark wordmark--large">Trevantiq</div>
  <div class="web-address">www.trevantiq.example</div>
</section>

</body>
</html>
```